website design + images

We need a very appealing website design, layout and images for a sales analytics and sales productivity services company based in San Ramon, California. We need a good design for the home page and a template for all other pages (total 2 designs), and images for all inner pages (center column/banner images, and right hand top corner small images). There are about 18 inner pages.
Updates

Our existing website is www.brightvale.com
Our corporate colours are the ones that are there on the website. The logo is also shown. We will be changing the tagline to "accelerating revenue" or equivalent of that.

Please use the document "website for brightvale - template v2.doc" that I just uploaded for any reference to the content, navigation and wireframes. A few more clarifications are provided mainly for the link "Solutions".

Rajesh Kothuri

Hi,
We just uploaded ver 4 of the website template. There is more elaboration provided around the sublinks / sections for Solutions. Pls review and do get back if you need any clarifications.

Rgds
Rajesh Kothuri

Hi all,
We have so far received a few good designs. The designs are more or less on the right track. I would like to urge all of you to use the content and navigation provided in the document attached to our brief "website for brightvale - template v4.doc".  Please DO NOT use the content in our existing website www.brightvale.com . That is very old. We mentioned it only for reference to colour theme and broad details.

We have totally 13 sections in Solutions pages. They may be designed as a tree of links - first level sublinks - second level sublinks or links - first level sublinks and the remaining as sections within the first level sublinks pages. The page design would remain the same for all inner pages except careers. But after finalizing the design for the inner page, we will need images for the different inner pages.

Rgds
Rajesh Kothuri

Hi,
Thank you all for participation and very good designs. We are quite happy with what we have seen. We have now shortlisted about 4 vendors and sending invididual feedback to them for further improvement. We will be finalizing by Monday or Tuesday.  To the vendors who do not get feedback from us, thank you very much for participation. We may still do business in future for some of our other needs. 
The following are the process steps / expectations going forward, 
1. Feedback to the shortlisted designers and inviting improvements.
2. Review of the improved designs and further shortlist & feedback or direct finalization.
3. The design should be in 1024*768
2. Number of page designs = 2 (home page, inner page).
4. Home page design: instead of delivery model and customers, show one link "Why Us".
4. Solutions page design:  We will be needing an image in center column of solutions page that in a nutshell gives all the different types of solutions we provide. The entire set of solutions is in our attached document website for brightvale - template v4 and I am just uploading v5 with more description on sublinks.
5. After selection, we will be needing images for all the solution pages (total 12 pages under solutions + one solutions page), 1 image for Why Us?, 1 for Careers, and 3 for company (about us/ team, core values, ...) = total 18

Rgds
Rajesh Kothuri

Target Market(s)

We are a sales analytics and sales productivity services company. We help B2B companies with: sales planning; sales operations and sales measurement. The characteristics of our customers are:
- B2B medium enterprises (USD 100M- USD 2B in revenue) in the US
- Primary target verticals are: high-tech, engineering and professional services firms
- Our primary target customers titles are VP of Sales or VP of marketing; we could be selling to the CEO at companies with revenues below $200M

Industry/Entity Type

Consulting

Requirements
Must have
• - Clean, uncluttered design
• - Easy navigation; minimum clicks
Nice to have
• We have already built a content management system and wireframes for this site. To the extent possible, it would be great to leverage the wireframe structure we built, provided you don’t have to compromise on the look and feel and navigation of the site. Below is what we currently have as banner sizes and resolutions are:
• Home page banner size: 950 * 250’
• All pages – center top - image size: 558 * 160
• All pages – right hand top image – 175*135’

```html
<!DOCTYPE html>
<html lang="en">
<head>
<meta charset="utf-8">
<title>Brightvale — Sales Planning Analytics: Campaign Planning</title>
<link rel="stylesheet" href="https://fonts.googleapis.com/css2?family=Open+Sans:wght@400;600;700&family=Roboto+Condensed:wght@700&display=swap">
<style>
  :root{
    --blue:#1a70b8;
    --blue-dark:#0d5a9e;
    --blue-text:#1566b0;
    --green:#4c9a3c;
    --green-dark:#3b7f2e;
    --text:#222;
    --rule:#bbb;
    --panel:#ffffff;
  }
  *{margin:0;padding:0;box-sizing:border-box}
  html,body{width:1200px;height:777px;overflow:hidden}
  body{
    position:relative;
    font-family:Arial, Helvetica, sans-serif;
    color:var(--text);
    background:linear-gradient(#ffffff 0px,#f4f4f4 160px,#dcdcdc 420px,#a9a9a9 640px,#9a9a9a 777px);
  }
  .utility-bar{
    position:absolute;left:0;top:0;width:1200px;height:41px;
    background:linear-gradient(var(--blue),var(--blue-dark));
    display:flex;align-items:flex-start;padding-left:54px;
  }
  .utility-bar a{
    display:flex;align-items:center;gap:6px;height:41px;white-space:nowrap;
    color:#fff;text-decoration:none;font-family:"Open Sans",sans-serif;
    font-size:13px;font-weight:600;letter-spacing:-.3px;margin-right:22px;
  }
  .utility-bar a.signin{
    background:linear-gradient(#6bb35a,#3f8c33);height:51px;width:161px;
    padding:0 0 10px 8px;border-radius:0 0 6px 6px;border:1px solid #8cc47c;border-top:0;
  }
  .utility-bar .ico{flex:none;width:20px;height:20px;border-radius:50%;background:#fff;display:flex;align-items:center;justify-content:center}

  .brand{position:absolute;left:62px;top:82px;font-family:"Open Sans",sans-serif;font-size:30px;font-weight:600;color:var(--blue);letter-spacing:0}

  .main-nav{position:absolute;right:78px;top:108px;display:flex;align-items:center;font-family:"Open Sans",sans-serif;font-weight:700;font-size:14px}
  .main-nav a{color:var(--blue-text);text-decoration:none;padding:0 6px}
  .main-nav a.active{background:linear-gradient(#5fae4d,#3d8a30);color:#fff;border-radius:13px;padding:2px 12px;border:2px solid #2f6f25;margin:0 4px}
  .main-nav .sep{color:var(--green);padding:0 2px}

  .panel{
    position:absolute;left:48px;top:157px;width:1090px;height:575px;background:var(--panel);
    border-radius:0 0 12px 12px;box-shadow:0 2px 8px rgba(0,0,0,.25);
  }

  .sidebar{position:absolute;left:57px;top:168px;width:215px}
  .side-head{
    height:37px;display:flex;align-items:center;gap:8px;padding-left:8px;
    background:linear-gradient(#fafafa,#d6d6d6);border-radius:4px 4px 0 0;
    font-family:"Roboto Condensed",sans-serif;font-weight:700;font-size:14.5px;color:var(--green);
    box-shadow:inset 0 -1px 0 #c9c9c9;
  }
  .side-head .box{width:16px;height:16px;background:var(--green);border:1px solid #2f6f25;display:flex;align-items:center;justify-content:center}
  .side-list{list-style:none;padding:6px 8px 8px 14px;background:linear-gradient(90deg,#fff 85%,#eee)}
  .side-list li{height:24.7px;display:flex;align-items:center;font-family:"Open Sans",sans-serif;font-size:11.5px;color:#222;border-bottom:1px dotted var(--rule)}
  .side-list li::before{content:"";width:4px;height:4px;border-right:1.5px solid #444;border-bottom:1.5px solid #444;transform:rotate(-45deg);margin:0 8px 0 2px}
  .side-list li.current{font-weight:600;color:#000}
  .side-list.tall li{padding-left:3px}

  .hero{position:absolute;left:284px;top:167px;width:626px;height:181px;
    background:linear-gradient(90deg,#0b5f9e 0%,#2a9fd8 45%,#6fd3ef 60%,#1b7ab8 100%)}
  .hero .copy{position:absolute;left:13px;top:95px;color:#fff;font-family:"Open Sans",sans-serif;text-shadow:0 1px 2px rgba(0,0,0,.4)}
  .hero .copy .big{font-size:24px;font-weight:700;letter-spacing:-.5px}
  .hero .copy .small{font-size:15px;font-weight:600;line-height:19px;letter-spacing:-.3px}

  .content{position:absolute;left:286px;top:358px;width:622px}
  .content h1{font-family:"Open Sans",sans-serif;font-weight:600;line-height:26px;margin-bottom:12px}
  .content h1 .kicker{display:block;color:var(--blue-text);font-size:20px;letter-spacing:-.3px}
  .content h1 .title{display:block;color:var(--green);font-size:24px;letter-spacing:-.3px}
  .content p{font-size:13.3px;line-height:18.2px;text-align:justify;margin-bottom:18px}

  .side-feature{position:absolute;left:926px;top:167px;width:196px}
  .side-feature .photo{height:152px;background:linear-gradient(135deg,#6d7f95,#d9dde3 55%,#a08a6c)}
  .side-feature .caption{height:29px;background:var(--green);color:#fff;font-family:"Roboto Condensed",sans-serif;font-weight:700;font-size:14px;display:flex;align-items:center;padding-left:8px}
  .side-text{position:absolute;left:926px;top:349px;width:196px;height:350px;border-left:1px solid #ddd;padding:14px 0 0 12px}
  .side-text p{font-size:13.1px;line-height:18.2px;text-align:justify;margin-bottom:18px}

  .site-footer{position:absolute;left:58px;right:78px;top:743px;display:flex;justify-content:space-between;color:#fff;font-size:13.5px}
  .site-footer a{color:#fff;text-decoration:none}
</style>
</head>
<body>
  <div class="utility-bar">
    <a class="signin" href="#"><span class="ico"><svg width="12" height="12" viewBox="0 0 12 12"><path d="M1 6h6M5 3l3 3-3 3M8 1h3v10H8" fill="none" stroke="#3f8c33" stroke-width="1.6"/></svg></span>SIGN IN / REGISTER</a>
    <a href="#"><span class="ico"><svg width="12" height="12" viewBox="0 0 12 12"><rect x="4" y="1" width="4" height="3" fill="none" stroke="#1a70b8" stroke-width="1.3"/><rect x="1" y="8" width="4" height="3" fill="none" stroke="#1a70b8" stroke-width="1.3"/><rect x="7" y="8" width="4" height="3" fill="none" stroke="#1a70b8" stroke-width="1.3"/><path d="M6 4v2M3 8V6h6v2" fill="none" stroke="#1a70b8" stroke-width="1.3"/></svg></span>CONTACT &nbsp;US</a>
    <a href="#"><span class="ico"><svg width="12" height="12" viewBox="0 0 12 12"><rect x="1" y="3" width="10" height="7" fill="none" stroke="#1a70b8" stroke-width="1.3"/><path d="M1 3l5 4 5-4" fill="none" stroke="#1a70b8" stroke-width="1.3"/></svg></span>SITEMAP</a>
  </div>

  <div class="brand">Brightvale</div>

  <nav class="main-nav">
    <a href="#">Home</a>
    <a class="active" href="#">Solutions</a>
    <a href="#">Why Us</a><span class="sep">|</span>
    <a href="#">Company</a><span class="sep">|</span>
    <a href="#">Careers</a>
  </nav>

  <div class="panel"></div>

  <aside class="sidebar">
    <div class="side-head"><span class="box"><svg width="8" height="6" viewBox="0 0 8 6"><path d="M0 0h8L4 6z" fill="#fff"/></svg></span>Sales Planning Analytics</div>
    <ul class="side-list">
      <li>Customer Targeting</li>
      <li>Territory Planning</li>
      <li class="current">Campaign Planning</li>
    </ul>
    <div class="side-head"><span class="box"><svg width="6" height="8" viewBox="0 0 6 8"><path d="M0 0l6 4-6 4z" fill="#fff"/></svg></span>Sales Productivity Centers</div>
    <ul class="side-list">
      <li>Quoting center</li>
      <li>Proposal center</li>
      <li>CRM center</li>
      <li>Partner center</li>
      <li>Reference center</li>
      <li>Deal center</li>
    </ul>
    <div class="side-head"><span class="box"><svg width="6" height="8" viewBox="0 0 6 8"><path d="M0 0l6 4-6 4z" fill="#fff"/></svg></span>Sales Measurement Analytics</div>
    <ul class="side-list tall">
      <li>Business Reporting</li>
      <li>Metrics &amp; Benchmarking</li>
      <li>Pipeline health check</li>
      <li>Sales rep scorecards</li>
      <li>What-if analyses</li>
      <li>Data services.</li>
    </ul>
  </aside>

  <div class="hero" role="img" aria-label="Banner photo: two businessmen shaking hands in front of a blue stock chart">
    <div class="copy">
      <div class="big">Do more with less.</div>
      <div class="small">No upfront software, hardware,<br>people or training costs for you. Pay as you go.</div>
    </div>
  </div>

  <main class="content">
    <h1><span class="kicker">Sales Planning Analytics:</span><span class="title">Campaign Planning</span></h1>
    <p>Lorem ipsum dolor sit amet, consectetur adipiscing elit. Proin augue felis, egestas quis imperdiet id, cursus sit amet est. Vestibulum consequat consectetur nisl non sodales. Donec viverra rhoncus turpis interdum aliquam. Ut imperdiet, risus varius aliquam lobortis, tortor quam hendrerit magna, imperdiet malesuada justo justo posuere mi. Praesent pretium consectetur tellus eu tempor. Duis iaculis sollicitudin mauris, eu posuere ligula dictum quis. Sed at lacus et dui condimentum ultrices. Aliquam cursus porta placerat. Suspendisse ut ante quam, lobortis laoreet ante. Aliquam ligula eros, bibendum rhoncus tristique sit amet, viverra a nunc. Cras aliquet, lectus eu facilisis tempor, lectus lacus vehicula felis, a tincidunt enim felis sit amet tellus.</p>
    <p>Fusce egestas, massa et placerat varius, urna odio elementum neque, aliquet mattis elit ipsum in ante. Maecenas mollis dolor id est vehicula et auctor turpis dignissim. Suspendisse lobortis eleifend lacus sit amet eleifend. Aenean a orci id mi scelerisque porttitor. Vestibulum lectus arcu, iaculis non iaculis ultrices, ultricies sit amet nisi. Nullam dictum nunc et metus dapibus scelerisque.</p>
  </main>

  <div class="side-feature">
    <div class="photo" role="img" aria-label="Photo: business documents and charts on a meeting table"></div>
    <div class="caption">Sales Operations Support</div>
  </div>
  <div class="side-text">
    <p>Vestibulum lectus arcu, iaculis non iaculis ultrices, ultricies sit amet nisi. Nullam dictum nunc et metus dapibus scelerisque. Etiam quis sapien in purus consequat ornare.</p>
    <p>Praesent vitae ipsum lorem. Nullam ac orci mi, sed pellentesque dolor. Nullam dictum nunc et metus dapibus scelerisque. Etiam quis sapien in purus consequat ornare. Praesent vitae ipsum lorem. Nullam ac orci mi, sed pellentesque dolor.</p>
  </div>

  <footer class="site-footer">
    <div><a href="#">Contact Us</a> | <a href="#">Sitemap</a> &nbsp;| &nbsp;<a href="#">Disclaimer</a></div>
    <div>© 2010. Brightvale, Inc. All Rights Reserved</div>
  </footer>
</body>
</html>
```